Global Consulting firm needs a Business Card Design (Contest)

We need a business card design for a company with global reach called 'Harborline Group'. Harborline Group is a Trusted Procurement Advisor that consults for Zenith 400 and Meridian 900 companies to find cost reductions in their spending. We would like to see designs that communicate fiduciary trust and sense of partnership. The Front should have our logo w/ 'trusted procurement advisor', Employee name and title, company address, email, phone and fax (logo attached "Harbor line group final"). The color scheme and basic concept should be consistent with our presentation front page (attached "HLG presentation cover page"). The Back should have our website (www.hlinellc.com) and an array of our areas of expertise: office supplies, lab supplies, wireless telecom, MRO and IT (see "lab supplies" file for example).

```html
<!DOCTYPE html>
<html lang="en">
<head>
<meta charset="utf-8">
<title>Harborline Group – Business Card</title>
<link rel="stylesheet" href="https://fonts.googleapis.com/css2?family=Noto+Serif:ital,wght@0,400;0,700;1,400&family=Arimo:wght@400&display=swap">
<style>
  :root {
    --backdrop: #2c2e31;
    --brand-brown: #8a3a17;
    --brand-brown-line: #9a4a25;
    --card-light: #fdf9f4;
    --card-tan: #ddb48f;
    --ink-dark: #2a1a12;
    --ink-brown: #7a3419;
    --contact-gold: #f4c24a;
    --white: #ffffff;
    --service-ink: #f3e2d6;
    --swirl-gold: #d9a14a;
    --swirl-rose: #b98a6f;
  }
  * { margin: 0; padding: 0; box-sizing: border-box; }
  html, body { width: 1200px; height: 957px; overflow: hidden; }
  body { background: var(--backdrop); position: relative; font-family: "Arimo", Arial, sans-serif; }

  .card { position: absolute; width: 617px; height: 350px; overflow: hidden; }

  /* Front */
  .card-front { left: 503px; top: 45px;
    background: linear-gradient(100deg, var(--card-light) 0%, #f6e8da 45%, var(--card-tan) 100%); }
  .front-brand { position: absolute; left: 35px; top: 28px; display: flex; align-items: center; gap: 7px; }
  .brand-dot { width: 34px; height: 34px; border-radius: 50%; background: var(--swirl-gold); flex: none; }
  .front-brand .brand-name { font-family: "Noto Serif", Georgia, serif; font-weight: 700; font-size: 27px; color: var(--ink-dark); }
  .front-tagline { position: absolute; left: 89px; top: 64px; font-family: "Noto Serif", Georgia, serif; font-style: italic; font-size: 14.5px; color: var(--ink-dark); }
  .person-name { position: absolute; left: 141px; width: 408px; top: 143px; text-align: center;
    font-family: "Noto Serif", Georgia, serif; font-weight: 400; font-size: 29px; color: var(--ink-dark); }
  .name-rule { position: absolute; left: 141px; right: 0; top: 184px; height: 1.5px; background: var(--brand-brown-line); }
  .person-title { position: absolute; left: 141px; width: 408px; top: 189px; text-align: center;
    font-size: 16px; color: var(--ink-brown); }
  .office-details { position: absolute; left: 141px; width: 408px; top: 232px; text-align: center;
    font-size: 13px; line-height: 18px; color: var(--ink-brown); }
  .contact-band { position: absolute; left: 0; right: 0; bottom: 0; height: 55px; background: var(--brand-brown);
    display: flex; align-items: center; padding-left: 30px; }
  .contact-item { display: flex; align-items: center; gap: 7px; color: var(--contact-gold); font-size: 16.5px; margin-right: 20px; white-space: nowrap; }
  .contact-item svg { flex: none; }

  /* Back */
  .card-back { left: 75px; top: 392px; background: var(--brand-brown); }
  .swirl-art { position: absolute; left: 0; top: 0; width: 380px; height: 350px;
    background: radial-gradient(ellipse 190px 200px at 150px 185px, var(--swirl-gold) 0%, #c99660 35%, var(--swirl-rose) 65%, rgba(138,58,23,0) 100%); }
  .back-brand { position: absolute; left: 95px; top: 100px; display: flex; align-items: center; gap: 9px; }
  .back-brand .brand-dot { width: 50px; height: 50px; }
  .back-brand .brand-name { font-family: "Noto Serif", Georgia, serif; font-weight: 700; font-size: 40px; color: var(--white); white-space: nowrap; }
  .back-tagline { position: absolute; left: 177px; top: 154px; font-family: "Noto Serif", Georgia, serif; font-style: italic;
    font-size: 22px; color: var(--white); }
  .services { position: absolute; right: 80px; top: 203px; list-style: none; text-align: right;
    font-size: 17px; line-height: 20.2px; color: var(--service-ink);
    border-right: 3px solid var(--white); padding-right: 6px; }
</style>
</head>
<body>

<section class="card card-front" aria-label="Card front">
  <div class="front-brand">
    <span class="brand-dot"></span>
    <span class="brand-name">Harborline Group</span>
  </div>
  <p class="front-tagline">Trusted Procurement Advisor</p>
  <h1 class="person-name">Daniel Ashford</h1>
  <div class="name-rule"></div>
  <p class="person-title">Marketing Manager</p>
  <p class="office-details">1200 Harbor Avenue, Suite 300, Portland, OR 97201<br>Fax (555) 014-2291</p>

  <div class="contact-band">
    <span class="contact-item">
      <svg width="20" height="26" viewBox="0 0 20 26" aria-hidden="true">
        <path d="M5 1 L9 6 L6.5 9 Q8 15 12 19 L15 17 L19 21 L15.5 25 Q3 20 1.5 5 Z" fill="var(--white)"/>
      </svg>
      (555) 014-2290
    </span>
    <span class="contact-item">
      <svg width="32" height="22" viewBox="0 0 32 22" aria-hidden="true">
        <rect x="1" y="1" width="30" height="20" fill="none" stroke="var(--white)" stroke-width="1.6"/>
        <path d="M1 1 L16 13 L31 1 M1 21 L12 10 M31 21 L20 10" fill="none" stroke="var(--white)" stroke-width="1.4"/>
      </svg>
      info@hlinellc.com
    </span>
    <span class="contact-item">
      <svg width="30" height="30" viewBox="0 0 30 30" aria-hidden="true">
        <circle cx="15" cy="15" r="14" fill="var(--white)"/>
        <path d="M7 8 Q11 6 13 9 Q12 13 9 13 Q8 17 5 15 Q4 11 7 8 Z M17 16 Q22 15 23 19 Q21 25 17 24 Q15 20 17 16 Z M18 5 Q23 6 25 10 Q21 11 18 8 Z" fill="var(--brand-brown)"/>
      </svg>
      www.hlinellc.com
    </span>
  </div>
</section>

<section class="card card-back" aria-label="Card back">
  <div class="swirl-art" role="img" aria-label="Soft gold and rose swirl decoration"></div>
  <div class="back-brand">
    <span class="brand-dot"></span>
    <span class="brand-name">Harborline Group</span>
  </div>
  <p class="back-tagline">Trusted Procurement Advisor</p>
  <ul class="services">
    <li>Office Supplies</li>
    <li>Lab Supplies</li>
    <li>Wireless Telecom</li>
    <li>MRO</li>
    <li>IT</li>
    <li>Shipping/Postage</li>
  </ul>
</section>

</body>
</html>
```